Web Design Project - Shipping Industry

Goals and Objectives
The objective of the new website is to create a more modern look and feel. The site will also allow for a more effective means of communicating with members while providing the public with information and developments in the local, regional and international shipping industry.
Scope
The website will highlight the history of the organisation inclusive of text and photographs. It will take visitors through the years from beginning to present. Information on the history of the shipping industry will also be included.
It will feature current articles on the organisation, its members and stakeholders in the shipping industry. Member information as well as pertinent details regarding the organisation’s subsidiaries will be documented for the website.
Information as it relates to shipping statistics, case studies, laws and regulations, international treaties and trade documents, shipping terms, careers in shipping, job opportunities, training opportunities, information for shippers including port listing and trade lanes will be main features of the content for the website.
The Association’s community involvement, industry calendar events and related links relevant industry members will also be featured.
Target Market
• The General Public;
• Members of the organization;
• Shipping Industry Stakeholders (local, regional and international);
• Tertiary students conducting research.
• Potential employees
• Potential Business Partners
Best Practice Bench Marketing
The following websites are being looked at:
• Korvel Quayworks - http://www.korvelquayworks.example/ (preferred look)
• Tessaly Maritime Association - http://www.tma-freight.example/ (like image transition on main page)
• Drovna - http://www.drovna.example (professional look)
• PLW - http://www.pelworth.example (preferred color: blue in logo)
• Quillo - http://www.quillo.example/electronics/tv-video-audio/ (preferred look for links page: image + short text below + visit site link)
Expected Result
• 3 - 5 pages which must include: [1] main page [2] standard page [3] links page

```html
<!DOCTYPE html>
<html lang="en">
<head>
<meta charset="utf-8">
<title>Corvane Freight</title>
<link rel="stylesheet" href="https://fonts.googleapis.com/css2?family=Source+Sans+3:ital,wght@0,400;0,600;1,400&display=swap">
<style>
:root{
  --frame:#27557f;
  --paper:#ffffff;
  --strip:#efefef;
  --nav-top:#3ea6df;
  --nav-bottom:#1b80c0;
  --nav-active:#25609a;
  --nav-line:#1870a8;
  --heading:#1f5186;
  --body-blue:#2f5d8c;
  --grey:#5c5c5c;
  --ink:#1a1a1a;
  --caption-bg:#eef7fd;
  --author-bg:#dcecf8;
  --dot:#5a83ad;
  --dot-active:#27557f;
}
*{box-sizing:border-box;margin:0;padding:0}
html,body{width:1086px;height:1200px;overflow:hidden}
body{background:var(--frame);font-family:"Source Sans 3",sans-serif;position:relative}
.page{position:absolute;left:19px;top:0;width:1048px;height:1143px;background:var(--paper)}
.page::before{content:"";position:absolute;left:0;top:0;width:100%;height:10px;background:var(--strip)}
.abs{position:absolute}
.wordmark{left:43px;top:52px;font-size:36px;font-weight:400;color:var(--ink);letter-spacing:.2px}
.search{left:763px;top:71px;width:279px;height:29px;display:flex;box-shadow:0 6px 6px -4px rgba(0,0,0,.25);border-radius:4px}
.search-field{flex:1;border:1px solid #d6d6d6;border-right:0;border-radius:4px 0 0 4px;font-style:italic;font-size:13px;color:#777;padding:6px 11px}
.search-btn{width:76px;background:linear-gradient(var(--nav-top),var(--nav-bottom));color:#fff;font-size:13px;display:flex;align-items:center;justify-content:center;border-radius:0 4px 4px 0}
.nav{left:34px;top:124px;width:1014px;height:50px;border-radius:6px;background:linear-gradient(var(--nav-top),var(--nav-bottom));display:flex;overflow:hidden;border:1px solid #1a6fa8}
.nav a{color:#fff;text-decoration:none;font-size:15px;display:flex;align-items:center;justify-content:center;border-right:1px solid var(--nav-line)}
.nav a:last-child{border-right:0}
.nav .active{background:var(--nav-active)}
.hero{left:34px;top:182px;width:1013px;height:414px;background:linear-gradient(180deg,#b9c9d8 0%,#7d8d9c 45%,#4a4f55 100%);border:1px solid #9fb7cc}
.caption{left:80px;top:395px;width:488px;height:159px;background:var(--caption-bg);border:1px solid #c9dbe9;padding:18px 22px 0 22px}
.caption h1{font-weight:600;font-size:23px;color:#173f66;letter-spacing:.2px;margin-bottom:6px;white-space:nowrap}
.caption p{font-size:14px;line-height:20px;color:#1e4a78;margin-bottom:5px}
.dots{left:983px;top:605px;display:flex;gap:4px}
.dots i{width:9px;height:9px;background:var(--dot);display:block}
.dots i:first-child{background:var(--dot-active)}
.welcome{left:43px;top:634px;width:710px}
.welcome h2,.testimonials h2{font-weight:400;font-size:20px;color:var(--heading);margin-bottom:10px}
.welcome p{font-size:12px;line-height:17px;color:var(--body-blue);margin-bottom:5px}
.service{top:886px;width:229px}
.service .thumb{height:119px}
.service h3{font-weight:400;font-size:14.5px;color:var(--heading);margin:8px 0 10px 2px}
.service p{font-size:12px;line-height:17px;color:var(--grey);padding-left:2px;width:210px}
.testimonials{left:778px;top:638px;width:270px}
.quote-lead{font-style:italic;font-size:14px;line-height:19px;color:#222;margin-bottom:6px;padding-left:2px}
.quote{font-style:italic;font-size:12px;line-height:17px;color:var(--grey);padding-left:2px}
.author{height:21px;background:var(--author-bg);color:var(--heading);font-size:12px;display:flex;align-items:center;padding-left:10px;margin-left:-5px}
.rule{border-top:2px dotted #7a7a7a;margin:16px 0 20px}
.touch{left:780px;top:1065px;display:flex;align-items:center;gap:4px;font-size:14px;color:#222}
.touch span{margin-right:6px}
.touch i{width:19px;height:19px;background:#3c8fd1;border-radius:2px;display:block}
.footer-links{left:28px;top:1164px;display:flex;font-size:12.5px;color:#fff}
.footer-links span{padding:0 14px;border-left:1px solid #fff;line-height:14px}
.footer-links span:first-child{padding-left:0;border-left:0}
.copyright{right:26px;top:1164px;font-size:12.5px;color:#fff}
</style>
</head>
<body>
<div class="page"></div>

<div class="abs wordmark">Corvane Freight</div>

<div class="abs search">
  <div class="search-field">search here..</div>
  <div class="search-btn">SEARCH</div>
</div>

<nav class="abs nav">
  <a class="active" style="width:104px">Home</a>
  <a style="width:128px">About Us</a>
  <a style="width:117px">Services</a>
  <a style="width:127px">Products</a>
  <a style="width:149px">Testimonials</a>
  <a style="width:148px">Recent Blog</a>
  <a style="width:124px">Location</a>
  <a style="width:115px">Contact</a>
</nav>

<div class="abs hero" role="img" aria-label="Photo of a truck loading cargo into the open nose of a large freight aircraft on an airport apron"></div>

<div class="abs caption">
  <h1>CORVANE FREIGHT PUNCH LINE GOES HERE..</h1>
  <p>Our Website Design team give an unforgettable impression on the customers and the clients.</p>
  <p>We can assure you that this is the best place for requirement of yours regarding website design solutions</p>
</div>

<div class="abs dots"><i></i><i></i><i></i><i></i><i></i></div>

<section class="abs welcome">
  <h2>Welcome to Our Website Mainpage</h2>
  <p>Brightmoor Webworks is a web service company, offering a wide range of services which range from designing and development, that is covering almost all the fields in the best possible way. To be the best we know what and how to present beautifully the working of the client’s need and their advantages be highlighted. We act in accordance with the Industry certified processes to deliver the best to our clients all over the world. Over years we have built a strong reputation in providing website design and web development services.</p>
  <p>Thus, Wanna get ahead in the competition with other websites…. Brightmoor Webworks provide you with an attractive and most convincing website to enhance your marketing goals.</p>
  <p>The only way to success is through the right path and that’s what we provide you. None of the other companies has the result we do. So stick to the best that’s how you will be the best don’t opt for the second best.</p>
</section>

<article class="abs service" style="left:42px">
  <div class="thumb" role="img" aria-label="Photo of stainless steel industrial processing equipment" style="background:linear-gradient(#d7dde2,#8e9aa3)"></div>
  <h3>Industry Services 1st</h3>
  <p>We here modify the site to improve the ranking by using the keywords and contents.</p>
</article>
<article class="abs service" style="left:283px">
  <div class="thumb" role="img" aria-label="Photo of close-up metal gears" style="background:linear-gradient(135deg,#2b2b2b,#9a9a94 55%,#3a3632)"></div>
  <h3>Industry Services 2nd</h3>
  <p>We here modify the site to improve the ranking by using the keywords and contents.</p>
</article>
<article class="abs service" style="left:525px">
  <div class="thumb" role="img" aria-label="Photo of wind turbines in a green field with cooling towers behind" style="background:linear-gradient(#b9d4ec 0%,#d9e6ee 45%,#4f8a3a 70%,#2f5d22 100%)"></div>
  <h3>Industry Services 3rd</h3>
  <p>We here modify the site to improve the ranking by using the keywords and contents.</p>
</article>

<aside class="abs testimonials">
  <h2>Testimonials</h2>
  <p class="quote-lead">Brightmoor Webworks is a professional website design company dedicated to provide excellent services.</p>
  <p class="quote" style="line-height:19px;margin-bottom:10px">We at Brightmoor Webworks think graphic design as a combination and collaboration of ideas and technology.</p>
  <div class="author">BY AUTHOR NAME</div>
  <div class="rule"></div>
  <p class="quote" style="margin-bottom:5px">Brightmoor Webworks is a professional website design company dedicated to provide excellent services. We at Brightmoor Webworks think graphic design as a combination and collaboration of ideas and technology.</p>
  <p class="quote" style="margin-bottom:16px">Our Website Design team give an unforgettable impression on the customers and the clients</p>
  <div class="author">BY AUTHOR NAME</div>
</aside>

<div class="abs touch"><span>Get In Touch</span><i></i><i></i><i></i><i></i></div>

<footer>
  <div class="abs footer-links"><span>home</span><span>about us</span><span>Services</span><span>Location</span><span>Contact</span></div>
  <div class="abs copyright">copyright © 2012 Company Name &nbsp;|&nbsp; All right reserved</div>
</footer>
</body>
</html>
```